Business Card Design for a Personal Trainer

I need a business card design for my job as a personal trainer. It should have a unique, modern and exclusive design. On the front there should be only my logo with my name and my job. 0162/3819204 Tobias Lendhart Wiesengrundweg 14 80417 Munich Germany The most important contact information is the web adress. it can be bigger than the rest, but its not necessary. The card should be 8,5cmx5,5cm big. Font: Roboto. Colors: black, white, gray, 56c1ff.

```html
<!DOCTYPE html>
<html lang="de">
<head>
<meta charset="UTF-8">
<title>Tobias Lendhart – Personal Trainer</title>
<link rel="stylesheet" href="https://fonts.googleapis.com/css2?family=Roboto:wght@300;400;500&display=swap">
<style>
  :root {
    --page-bg: #e6e6e6;
    --card-light: #ffffff;
    --card-mist: #ecebeb;
    --ink: #111111;
    --band: #050505;
    --on-band: #f2f2f2;
    --photo-dark: #2b2b2b;
    --photo-mid: #8a8a8a;
    --photo-light: #d9d9d9;
  }
  * { margin: 0; padding: 0; box-sizing: border-box; }
  html, body {
    width: 1200px; height: 900px; overflow: hidden;
    background: var(--page-bg);
    font-family: 'Roboto', sans-serif;
  }
  .card {
    position: absolute; left: 100px; top: 126px;
    width: 1000px; height: 647px; overflow: hidden;
    background: linear-gradient(180deg, var(--card-light) 0%, var(--card-mist) 100%);
    box-shadow: 0 12px 34px rgba(0,0,0,0.18);
  }
  .contact-band {
    position: absolute; left: 360px; top: 315px;
    width: 640px; height: 332px; background: var(--band);
  }
  .portrait {
    position: absolute; left: 0; top: 30px; width: 476px; height: 617px;
    background: radial-gradient(ellipse at 50% 30%, var(--photo-light) 0%, var(--photo-mid) 35%, var(--photo-dark) 75%);
    border-radius: 200px 200px 0 0;
  }
  .brand {
    position: absolute; left: 476px; width: 524px; top: 92px;
    display: flex; justify-content: center; align-items: center; gap: 14px;
    font-weight: 500; font-size: 44px; letter-spacing: 4px; color: var(--ink);
  }
  .brand-square { width: 26px; height: 26px; background: var(--ink); }
  .name {
    position: absolute; left: 430px; width: 620px; top: 206px;
    text-align: center; font-weight: 400; font-size: 46px; letter-spacing: 1px;
    color: var(--ink);
  }
  .role {
    position: absolute; left: 440px; width: 460px; top: 269px;
    display: flex; align-items: center; gap: 10px;
    font-size: 19px; font-weight: 400; letter-spacing: 5px; color: var(--ink);
  }
  .role::before, .role::after { content: ""; flex: 1; height: 2px; background: var(--ink); }
  .contact-list { position: absolute; left: 522px; top: 348px; list-style: none; }
  .contact-list li {
    display: flex; align-items: center; gap: 10px; height: 41px;
    font-size: 31px; font-weight: 400; color: var(--on-band);
  }
  .contact-list svg { width: 28px; height: 28px; fill: var(--on-band); }
  .address {
    position: absolute; left: 522px; top: 486px;
    font-size: 30px; line-height: 42px; font-weight: 400; color: var(--on-band);
    font-style: normal;
  }
</style>
</head>
<body>
  <section class="card">
    <div class="contact-band"></div>
    <div class="portrait" role="img" aria-label="Black and white portrait of the trainer, arms crossed, in a dark sports shirt"></div>

    <div class="brand"><span class="brand-square"></span>LENDHART</div>
    <h1 class="name">TOBIAS LENDHART</h1>
    <p class="role">PERSONAL TRAINER</p>

    <ul class="contact-list">
      <li>
        <svg viewBox="0 0 24 24" aria-hidden="true"><path d="M3 9c0-3 4-5 9-5s9 2 9 5v1h-5V8.5c-1-.5-2.5-.7-4-.7s-3 .2-4 .7V10H3zM6 11h12l2 8H4zm6 2a2.5 2.5 0 1 0 0 5 2.5 2.5 0 0 0 0-5z"/></svg>
        0162/3819204
      </li>
      <li>
        <svg viewBox="0 0 24 24" aria-hidden="true"><path d="M2 5h20v14H2zm2 2v.5l8 5.5 8-5.5V7zm0 3v7h16v-7l-8 5.5z"/></svg>
        t.lendhart@postfeld.de
      </li>
      <li>
        <svg viewBox="0 0 24 24" aria-hidden="true"><circle cx="12" cy="12" r="10"/><path fill="#050505" d="M7 7c2 0 3 1 3 2s-2 1-2 3 2 2 2 4-1 2-2 2c-1-2-3-3-3-6s1-3 2-5zm8 1c2 0 3 2 3 4s-1 3-2 3-2-1-2-2 1-2 0-3-1-2 1-2z"/></svg>
        www.tobiaslendhart.de
      </li>
    </ul>

    <address class="address">Wiesengrundweg 14<br>80417 München</address>
  </section>
</body>
</html>
```